New Business Card Design Project LORVANTI-Italy

we are LORVANTI-Italy
our company in the market for 3 years we are luxury cosmetic company and its about time for a facelift :)
i will like to have elegant luxurious and unique business card
that will give the person that get it a unique, luxurious and elegant impression
I'm VERY OPEN FOR NEW IDEAS , even duo i add a few files of things that i see on line and i like them

i add my logo as well
my website is LORVANTI.COM
(if you would like to see the main style that we have)

Target Market(s)

adult that have money :)

Industry/Entity Type

Business

Contact Information for Business Card

Name - Dario Lorvanti
Position - CEO and CO Founder
address - 4817 E Halvern
telephone - 555-384-1926
email - dario@lorvanti.com
fax - 555-384-1926
website - LORVANTI.COM

Colors
000000
959595
fbee3e
ffffff

Requirements
Must have
• big logo in GOLD color
• elegant look
• impressive
Nice to have
• not must but maybe classy pattern background
• not must but maybe emblem
• maybe clear plastic business card
Should not have
• colors
• images

```html
<!DOCTYPE html>
<html lang="en">
<head>
<meta charset="utf-8">
<title>LORVANTI Italy – Business Card</title>
<link rel="stylesheet" href="https://fonts.googleapis.com/css2?family=Roboto:wght@400;700&display=swap">
<style>
  :root {
    --backdrop: #2a2a2a;
    --card: #1c1c1c;
    --card-edge: #262626;
    --gold: #d9b23c;
    --gold-light: #f0d469;
    --white: #ffffff;
    --grey: #959595;
  }
  * { margin: 0; padding: 0; box-sizing: border-box; }
  html, body { width: 1200px; height: 900px; overflow: hidden; }
  body {
    background: var(--backdrop);
    font-family: "Roboto", Arial, sans-serif;
    position: relative;
  }
  .card {
    position: absolute;
    left: 290px;
    width: 620px;
    height: 354px;
    background: var(--card);
    border: 1px solid var(--card-edge);
    box-shadow: 0 10px 28px rgba(0,0,0,.45);
  }
  .card-front { top: 76px; }
  .card-back { top: 470px; }

  /* front */
  .brand {
    position: absolute;
    left: 0; right: 0; top: 84px;
    display: flex; flex-direction: column; align-items: center;
  }
  .brand-dot {
    width: 74px; height: 74px;
    border: 3px solid var(--gold);
    border-radius: 50%;
    margin-bottom: 22px;
  }
  .brand-name {
    color: var(--gold);
    font-weight: 700;
    font-size: 40px;
    letter-spacing: 4px;
  }
  .brand-origin {
    color: var(--gold);
    font-weight: 700;
    font-size: 13px;
    letter-spacing: 4px;
    margin-top: 8px;
    padding-top: 8px;
    border-top: 2px solid var(--gold);
    width: 230px;
    text-align: center;
  }

  /* back */
  .holder { position: absolute; left: 62px; top: 64px; }
  .holder-name {
    color: var(--gold);
    font-weight: 700;
    font-size: 24px;
    letter-spacing: .5px;
  }
  .holder-role {
    color: var(--white);
    font-size: 15px;
    margin-top: 4px;
  }
  .contact {
    position: absolute; left: 62px; top: 182px;
    list-style: none;
    color: var(--white);
    font-size: 15px;
  }
  .contact li {
    display: flex; align-items: center;
    height: 26px;
  }
  .contact .address { margin-bottom: 4px; }
  .contact svg { width: 16px; height: 16px; margin-right: 10px; fill: var(--gold); flex: none; }
  .seal {
    position: absolute; right: 56px; bottom: 46px;
    width: 124px; height: 124px;
    border-radius: 50%;
    border: 4px solid var(--gold);
  }
</style>
</head>
<body>
  <section class="card card-front">
    <div class="brand">
      <div class="brand-dot"></div>
      <div class="brand-name">LORVANTI</div>
      <div class="brand-origin">ITALY</div>
    </div>
  </section>

  <section class="card card-back">
    <div class="holder">
      <div class="holder-name">DARIO LORVANTI</div>
      <div class="holder-role">CEO &amp; CO Founder</div>
    </div>
    <ul class="contact">
      <li class="address">4817 E Halvern</li>
      <li>
        <svg viewBox="0 0 16 16" aria-hidden="true"><path d="M3.5 1l2.5 3-1.5 2c1 2 2.5 3.5 4.5 4.5l2-1.5 3 2.5-1.5 2.5C7 14 2 9 1 2.5z"/></svg>
        555-384-1926
      </li>
      <li>
        <svg viewBox="0 0 16 16" aria-hidden="true"><rect x="4" y="1" width="8" height="5"/><rect x="1" y="6" width="14" height="6" rx="1"/><rect x="4" y="11" width="8" height="4"/></svg>
        555-384-1926
      </li>
      <li>
        <svg viewBox="0 0 16 16" aria-hidden="true"><path d="M1 3h14v10H1z M2 4l6 5 6-5" fill="none" stroke="#d9b23c" stroke-width="1.6"/></svg>
        dario@lorvanti.com
      </li>
      <li>
        <svg viewBox="0 0 16 16" aria-hidden="true"><circle cx="8" cy="8" r="7"/><path d="M1 8h14M8 1c-3 3-3 11 0 14M8 1c3 3 3 11 0 14" fill="none" stroke="#1c1c1c" stroke-width="1.2"/></svg>
        LORVANTI.COM
      </li>
    </ul>
    <div class="seal"></div>
  </section>
</body>
</html>
```